design a construction company business card

Design business card around our logo. Card must have all the typical info: name, title, address, phone, email, business name, etc. Somewhere on the card I would like to see our motto "Built on integrity... Inspired by commitment." Consider adding a splash of bright orange to the card to complement the blues and silvers/grays in the logo. We are open to metallic inks, textures, etc. We would like to see options on both light and dark backgrounds. The font in the logo is Euro Technic Extended Regular.

```html
<!DOCTYPE html>
<html lang="en">
<head>
<meta charset="UTF-8">
<title>Halden Contracting – Business Card</title>
<link rel="stylesheet" href="https://fonts.googleapis.com/css2?family=Oswald:wght@400&family=Orbitron:wght@500&display=swap">
<style>
  :root {
    --backdrop: #2b2d31;
    --card: #eef0f2;
    --card-edge: #dfe2e6;
    --blue: #1c6fc4;
    --blue-deep: #12508f;
    --orange: #f07a12;
    --rule: #8f8fd0;
    --skyline-light: #dde3ee;
    --skyline-mid: #a9b6cf;
  }
  * { box-sizing: border-box; margin: 0; padding: 0; }
  html, body {
    width: 1200px;
    height: 900px;
    overflow: hidden;
    background: var(--backdrop);
  }
  .stage {
    width: 1200px;
    height: 900px;
    display: flex;
    align-items: center;
    justify-content: center;
  }
  .business-card {
    position: relative;
    width: 900px;
    height: 514px;
    background: linear-gradient(160deg, var(--card) 0%, var(--card-edge) 100%);
    font-family: "Oswald", "Arial Narrow", sans-serif;
    color: var(--blue);
  }
  .contact-person {
    position: absolute;
    left: 44px;
    top: 60px;
    font-size: 30px;
    line-height: 1.42;
  }
  .brand-name {
    position: absolute;
    left: 420px;
    top: 62px;
    font-size: 34px;
    letter-spacing: 2px;
    text-transform: uppercase;
    color: var(--blue);
  }
  .contact-lines {
    position: absolute;
    right: 44px;
    top: 228px;
    text-align: right;
    font-size: 30px;
    line-height: 1.4;
  }
  .skyline {
    position: absolute;
    left: 370px;
    top: 200px;
    width: 200px;
    height: 220px;
    background: linear-gradient(180deg, var(--skyline-light) 0%, var(--skyline-mid) 100%);
    border-radius: 2px;
  }
  .divider {
    position: absolute;
    left: 0;
    top: 0;
  }
  .motto {
    position: absolute;
    font-family: "Orbitron", sans-serif;
    font-weight: 500;
    font-size: 21px;
    color: var(--orange);
  }
  .motto--first { left: 44px; top: 404px; }
  .motto--second { right: 44px; top: 452px; }
</style>
</head>
<body>
<main class="stage">
  <section class="business-card">
    <div class="contact-person">
      <p class="person-name">John Smith</p>
      <p class="person-title">Job Title</p>
      <p class="person-address">1 Street Name, Suburb of State</p>
    </div>

    <p class="brand-name">Halden Contracting, Inc.</p>

    <div class="skyline" role="img" aria-label="Abstract skyline of tall buildings"></div>

    <svg class="divider" width="900" height="514" viewBox="0 0 900 514" aria-hidden="true">
      <line x1="90" y1="388" x2="380" y2="388" stroke="var(--rule)" stroke-width="3"/>
      <line x1="560" y1="432" x2="860" y2="432" stroke="var(--rule)" stroke-width="3"/>
    </svg>

    <div class="contact-lines">
      <p class="phone-mobile">0400000000</p>
      <p class="phone-office">0200000000</p>
      <p class="email">email@emailaddress.com</p>
    </div>

    <p class="motto motto--first">Built on integrity</p>
    <p class="motto motto--second">Inspired by commitment</p>
  </section>
</main>
</body>
</html>
```